verdant terraces simple classy business card design

my name is colin barrow and I run a gardening business aimed at high class verdant terraces. the business name is verdant terraces and our logo was designed on pixel harbour .My clientel are anything from residential homes to businesses. I take pride in my work and know that I offer a service like no other in my area.
The business card will be used to represent my business and I want it to be not only rememberable, but simplistic and modern. Eye catching too. Of course I would like it relatable to gardening and appealing to the correct clientel - those being garden enthusiasts, prestigious homes and businesses that are after top of the line gardening services like no other on the market.
I am not a typical lawn mowing business so I don't want a typical card design that represents that. The gardens I work with are generally million dollar properties with owners who are very garden proud looking for upkeep and guidance from me along with sometimes whole new garden designs. I want the business cards to show to my clients that I take pride, as they do, in their garden. And I want them to know from my card that I am a professional, qualified horticulturist offering them a top of the line service for life. I want them to refer my business on. I want them to look at my business card and see class and professionalism in a modern unique bold way.
The card should be simple with the possibility of the logo on the front being embossed/debossed and my details on the back the card should have a organic garden feel it's very important to me that it is absolutely perfect
I am also very open to ideas and suggestions so look forward to seeing the designs. the business logo has been supplied with this project and I want the card to be double sided

Contact info is
Colin Barrow - Managing Director / Horticulturist
Phone : 0481 526 704
Email: colinbarrow@verdantterraces.example.au

Target Market(s)

high class gardens residential and commercial

Industry/Entity Type

Gardener

Contact Information for Business Card

Contact info is
Phone : 0481 526 704

PLEASE MAKE CARD DOUBLE SIDED

Requirements
Must have
• organic simple classy modern feel
• must flow with the current logo that has been supplied with this project
• Double sided
• Must explain in a simple way that I deal with high end gardens and I'm a qualified horticulturist
Nice to have
• embossed debossed logo
Should not have
• shouldn't be to busy or cheap looking

```html
<!DOCTYPE html>
<html lang="en">
<head>
<meta charset="utf-8">
<title>Verdant Terraces — Business Card</title>
<link rel="stylesheet" href="https://fonts.googleapis.com/css2?family=PT+Sans:wght@400;700&display=swap">
<style>
  :root {
    --bg-top: #2c2c2c;
    --bg-bottom: #040404;
    --card: #ffffff;
    --green: #4f9a3f;
    --green-rule: #a9cf9c;
    --ink: #454545;
  }
  * { margin: 0; padding: 0; box-sizing: border-box; }
  html, body { width: 1200px; height: 900px; overflow: hidden; }
  body {
    background: linear-gradient(180deg, var(--bg-top) 0%, #151515 55%, var(--bg-bottom) 100%);
    font-family: "PT Sans", Arial, sans-serif;
    position: relative;
  }
  .card {
    position: absolute;
    top: 306px;
    width: 440px;
    height: 271px;
    background: var(--card);
    border-radius: 12px;
  }
  .card--back { left: 149px; }
  .card--front { left: 608px; }

  .wordmark {
    position: absolute;
    left: 0; right: 0;
    text-align: center;
    color: var(--green);
    font-weight: 700;
    text-transform: uppercase;
    line-height: 1.05;
  }
  .card--back .wordmark { top: 60px; font-size: 30px; letter-spacing: 2px; }
  .wordmark__line { display: block; }
  .wordmark__line--second { letter-spacing: 12px; font-size: 20px; margin-top: 2px; }

  .address {
    position: absolute;
    left: 28px; top: 157px;
    font-size: 12.5px;
    line-height: 15px;
    color: var(--ink);
  }
  .rule {
    position: absolute;
    left: 31px; right: 26px; top: 192px;
    height: 1px;
    background: var(--green-rule);
  }
  .person {
    position: absolute;
    right: 26px; top: 173px;
    text-align: right;
  }
  .person__name { color: var(--green); font-weight: 700; font-size: 15px; line-height: 18px; }
  .person__role { color: var(--ink); font-size: 12.5px; margin-top: 6px; }

  .contacts {
    position: absolute;
    left: 28px; top: 200px;
    list-style: none;
    font-size: 12.5px;
    color: var(--ink);
  }
  .contacts li { display: flex; align-items: center; height: 16px; }
  .contacts svg { width: 9px; height: 9px; margin-right: 7px; fill: var(--green); }

  .front-mark {
    position: absolute;
    left: 50%; top: 74px;
    width: 72px; height: 72px;
    margin-left: -34px;
    border-radius: 50%;
    background: var(--green);
  }
  .card--front .wordmark { top: 146px; font-size: 30px; letter-spacing: 2px; }
</style>
</head>
<body>
  <section class="card card--back" aria-label="Card back with contact details">
    <h1 class="wordmark">
      <span class="wordmark__line">Verdant</span>
      <span class="wordmark__line wordmark__line--second">Terraces</span>
    </h1>
    <p class="address">12345, Address Goes Here<br>Country Name, 123456.</p>
    <div class="person">
      <p class="person__name">Colin Barrow</p>
      <p class="person__role">Managing Director</p>
    </div>
    <div class="rule"></div>
    <ul class="contacts">
      <li><svg viewBox="0 0 10 10"><path d="M2 0.5 L3.6 0.5 L4.3 2.8 L3.2 3.7 C3.8 5 5 6.2 6.3 6.8 L7.2 5.7 L9.5 6.4 L9.5 8 C9.5 9 8.7 9.6 7.8 9.5 C4 9 1 6 0.5 2.2 C0.4 1.3 1 0.5 2 0.5 Z"/></svg>0481 526 704</li>
      <li><svg viewBox="0 0 10 10"><path d="M0.5 2 H9.5 V8.5 H0.5 Z M0.5 2 L5 5.5 L9.5 2" stroke="#fff" stroke-width="0.8"/></svg>colinbarrow@verdantterraces.example.au</li>
      <li><svg viewBox="0 0 10 10"><circle cx="5" cy="5" r="4.5"/></svg>www.verdantterraces.example.au</li>
    </ul>
  </section>

  <section class="card card--front" aria-label="Card front with business name">
    <div class="front-mark"></div>
    <h2 class="wordmark">
      <span class="wordmark__line">Verdant</span>
      <span class="wordmark__line wordmark__line--second">Terraces</span>
    </h2>
  </section>
</body>
</html>
```